Wordpress theme website for professionals working together

My partner and I are offering business services, my wife in the energy business as mainly as member of the board of commissioners. I am working as interim manager/consultant in the accounting and finance area. Both activities are connected in one company VELMOT BV (dutch ltd). We need a CV based website. Beside this we do some financial and accounting services.

Target Market(s)

small medium business

Font styles to use
Sans Serif

Colors

Designer to choose colors to be used in the design.

Requirements
Must have
• Pictures of both members.
• CLEAN AND SIMPLE
• I LIKE BLACK & WHITE
Nice to have
• I like design like this theme: http://theme.pruxelo-example.com/resume/

```html
<!DOCTYPE html>
<html lang="en">
<head>
<meta charset="utf-8">
<title>VELMOT BV – Resume</title>
<link rel="stylesheet" href="https://fonts.googleapis.com/css2?family=Montserrat:wght@400;600;700;800&family=Open+Sans:wght@400;600&family=Cormorant+Garamond:wght@500&family=Great+Vibes&display=swap">
<style>
:root{
  --black:#000;
  --ink:#111;
  --white:#fff;
  --grey-text:#777;
  --light-text:#bbb;
  --rule:#ddd;
  --skills-bg:#e9e9e9;
  --bar-track:#bdbdbd;
  --card-bg:#f3f0ef;
  --contact-bg:#f5f2f1;
  --social:#2a74c9;
}
*{margin:0;padding:0;box-sizing:border-box}
html,body{width:1200px;height:4147px;overflow:hidden}
body{position:relative;background:var(--white);font-family:"Open Sans",Arial,sans-serif;color:var(--ink)}
.abs{position:absolute}
.heading{font-family:"Montserrat",Arial,sans-serif;font-weight:800;font-size:22px;letter-spacing:.5px;text-transform:uppercase}
.heading-rule{position:absolute;height:3px;width:46px;background:#bbb}
.center{text-align:center;left:0;width:1200px}

/* header */
.site-header{top:0;left:0;width:1200px;height:88px;background:var(--white)}
.brand{left:147px;top:24px;font-family:"Montserrat",sans-serif;font-size:36px;font-weight:600;letter-spacing:1px;white-space:nowrap}
.main-nav{top:0;left:0;width:1200px;height:88px;font-family:"Montserrat",sans-serif;font-size:12px;font-weight:600;color:var(--ink)}
.nav-link{position:absolute;top:38px;white-space:nowrap;color:var(--ink)}
.nav-link.active{border-bottom:2px solid var(--ink);padding-bottom:6px}
.partner-btn{left:976px;top:33px;width:78px;height:26px;border:2px solid var(--ink);font-family:"Montserrat",sans-serif;font-size:11px;font-weight:600;text-align:center;line-height:22px}

/* hero */
.hero{top:88px;left:0;width:1200px;height:637px;background:var(--black);color:var(--white)}
.hero-photo{left:663px;top:0;width:537px;height:637px;background:radial-gradient(ellipse at 55% 40%,#8a8a8a 0%,#444 45%,#111 85%)}
.hero-name{left:185px;top:80px;font-family:"Cormorant Garamond",serif;font-size:60px;font-weight:500;letter-spacing:2px;white-space:nowrap}
.hero-meta{left:185px;font-family:"Montserrat",sans-serif;font-size:11.5px;white-space:nowrap}
.hero-meta .label{color:#666;display:inline-block;width:103px}
.hero-text{left:185px;top:252px;width:420px;font-size:13.5px;line-height:19.5px;color:#999}
.hero-sign{left:185px;top:470px;font-family:"Great Vibes",cursive;font-size:54px;white-space:nowrap}

/* jobs */
.jobs-divider{left:600px;top:725px;width:1px;height:525px;background:var(--rule)}
.job{width:300px}
.job-arrow{position:absolute;left:-41px;top:2px;width:22px;height:22px;border:1px solid #999}
.job-title{font-family:"Montserrat",sans-serif;font-weight:700;font-size:14px;text-transform:uppercase;white-space:nowrap}
.job-text{font-size:13px;line-height:16px;color:#444;margin-top:4px}

/* skills */
.skills{top:1250px;left:0;width:1200px;height:547px;background:linear-gradient(135deg,#f0f0f0,#dedede 50%,#ececec)}
.skill{width:215px}
.skill-label{font-size:14px;color:#222;white-space:nowrap}
.skill-icon{position:absolute;right:0;top:2px}
.skill-track{position:absolute;top:24px;left:0;width:215px;height:8px;background:var(--bar-track)}
.skill-fill{height:8px;background:var(--black)}
.skill-badge{position:absolute;top:36px;height:18px;width:30px;background:var(--black);color:var(--white);font-family:"Montserrat",sans-serif;font-size:10px;font-weight:700;text-align:center;line-height:18px}

/* education */
.timeline-line{left:599px;top:2002px;width:3px;height:605px;background:var(--black)}
.degrees-badge{left:509px;top:1969px;width:182px;height:33px;background:var(--black);color:var(--white);font-family:"Montserrat",sans-serif;font-size:12px;font-weight:700;text-align:center;line-height:33px}
.timeline-dot{width:20px;height:20px;border:4px solid var(--black);background:var(--white);border-radius:50%}
.timeline-end{left:593px;top:2603px;width:16px;height:16px;border-radius:50%;background:var(--black)}
.year{font-family:"Montserrat",sans-serif;font-weight:700;font-size:17px}
.edu-card{background:var(--card-bg);padding:40px 40px 30px;font-size:13px;line-height:16px;color:#555}
.edu-card h3{font-family:"Montserrat",sans-serif;font-size:14px;color:#222;margin-bottom:10px}

/* portfolio */
.portfolio-band{top:2704px;left:0;width:1200px;height:141px;background:var(--black);color:var(--white)}
.tile{width:300px;height:293px}

/* contact */
.contact{top:3431px;left:0;width:1200px;height:567px;background:var(--contact-bg)}
.contact-text{left:147px;top:3606px;width:320px;font-size:13px;line-height:16px;color:#555}
.contact-item{left:147px;width:330px;height:44px}
.contact-icon{position:absolute;left:0;top:4px;width:30px;height:30px;border-radius:50%;background:var(--black)}
.contact-label{position:absolute;left:44px;top:0;font-family:"Montserrat",sans-serif;font-size:11px;color:#555;white-space:nowrap}
.contact-value{position:absolute;left:44px;top:14px;font-family:"Montserrat",sans-serif;font-size:18px;font-weight:700;white-space:nowrap}
.field{background:var(--white);border:1px solid #ccc;font-size:13px;color:#555;padding:12px 14px}
.send-btn{left:523px;top:3865px;width:118px;height:44px;background:var(--black);color:var(--white);font-family:"Montserrat",sans-serif;font-weight:700;font-size:15px;text-align:center;line-height:44px}

/* footer */
.site-footer{top:3998px;left:0;width:1200px;height:149px;background:var(--black);color:var(--white)}
.footer-brand{left:147px;top:55px;font-family:"Montserrat",sans-serif;font-size:34px;font-weight:600;letter-spacing:1px;white-space:nowrap}
.follow{left:506px;top:70px;font-family:"Montserrat",sans-serif;font-size:11px;font-weight:700;white-space:nowrap}
.social{top:64px;width:26px;height:26px;border-radius:50%;background:var(--social)}
.copyright{left:860px;top:72px;font-size:11px;color:#ccc;white-space:nowrap}
</style>
</head>
<body>

<header class="site-header abs">
  <div class="brand abs">VELMOT BV</div>
  <nav class="main-nav abs">
    <span class="nav-link active" style="left:415px">HOME</span>
    <span class="nav-link" style="left:481px">SKILLS</span>
    <span class="nav-link" style="left:556px">EXPERIENCE</span>
    <span class="nav-link" style="left:666px">EDUCATION</span>
    <span class="nav-link" style="left:771px">PORTFOLIO</span>
    <span class="nav-link" style="left:874px">CONTACT</span>
  </nav>
  <div class="partner-btn abs">MARIT</div>
</header>

<section class="hero abs">
  <div class="hero-photo abs" role="img" aria-label="Black and white portrait photo of Hendrik"></div>
  <h1 class="hero-name abs">HENDRIK</h1>
  <div class="hero-meta abs" style="top:160px"><span class="label">WORKED FOR</span>: &nbsp;LINDQVIST ADVOCATEN &amp; NOTARISSEN &nbsp;| &nbsp;BRAMSTEDE AUDIT</div>
  <div class="hero-meta abs" style="top:185px"><span class="label">OTHER</span>: &nbsp;FOTOGRAPHY</div>
  <p class="hero-text abs">Lorem Ipsum is simply dummy text of the printing and typesetting industry. Lorem Ipsum has been the industry's standard dummy text ever since the 1500s, when an unknown printer took a galley of type and scrambled it to make a type specimen book. It has survived not only five centuries, but also the leap into electronic typesetting, remaining essentially unchanged. It was popularised in the 1960s with the release of Letraset sheets containing Lorem Ipsum passages, and more recently with desktop publishing software.</p>
  <div class="hero-sign abs">Hendrik</div>
</section>

<section class="jobs">
  <h2 class="heading abs" style="left:144px;top:800px">Actual Jobs</h2>
  <div class="heading-rule" style="left:144px;top:840px"></div>
  <h2 class="heading abs" style="left:736px;top:800px">Finished Jobs</h2>
  <div class="heading-rule" style="left:736px;top:840px"></div>
  <div class="jobs-divider abs"></div>

  <div class="job abs" style="left:199px;top:898px"><span class="job-arrow"><svg width="20" height="20"><path d="M8 6l4 4-4 4" fill="none" stroke="#333" stroke-width="1.5"/></svg></span><div class="job-title">Advisor RVK</div><div class="job-text">Lorem Ipsum is simply dummy text of the printing and typesetting industry</div></div>
  <div class="job abs" style="left:199px;top:1003px"><span class="job-arrow"><svg width="20" height="20"><path d="M8 6l4 4-4 4" fill="none" stroke="#333" stroke-width="1.5"/></svg></span><div class="job-title">Advisor Hale &amp; Norden</div><div class="job-text">Lorem Ipsum is simply dummy text of the printing and typesetting industry</div></div>

  <div class="job abs" style="left:791px;top:898px"><span class="job-arrow"><svg width="20" height="20"><path d="M8 6l4 4-4 4" fill="none" stroke="#333" stroke-width="1.5"/></svg></span><div class="job-title">Controller A.I. RVK</div><div class="job-text">Lorem Ipsum is simply dummy text of the printing and typesetting industry</div></div>
  <div class="job abs" style="left:791px;top:1003px"><span class="job-arrow"><svg width="20" height="20"><path d="M8 6l4 4-4 4" fill="none" stroke="#333" stroke-width="1.5"/></svg></span><div class="job-title">Advisor Ostara Green</div><div class="job-text">Lorem Ipsum is simply dummy text of the printing and typesetting industry</div></div>
  <div class="job abs" style="left:791px;top:1108px"><span class="job-arrow"><svg width="20" height="20"><path d="M8 6l4 4-4 4" fill="none" stroke="#333" stroke-width="1.5"/></svg></span><div class="job-title">Financial Director EVD</div><div class="job-text">Lorem Ipsum is simply dummy text of the printing and typesetting industry</div></div>
</section>

<section class="skills abs">
  <h2 class="heading abs center" style="top:66px">Skills</h2>
  <div class="heading-rule" style="left:577px;top:106px"></div>

  <div class="skill abs" style="left:227px;top:180px"><span class="skill-label">Annual reporting</span><svg class="skill-icon" width="14" height="16"><rect x="1" y="1" width="12" height="14" fill="#555"/><path d="M4 6h6M4 9h6M4 12h6" stroke="#ddd"/></svg><div class="skill-track"><div class="skill-fill" style="width:90%"></div></div><div class="skill-badge" style="left:164px">90%</div></div>
  <div class="skill abs" style="left:503px;top:180px"><span class="skill-label">Financial monthly reporting</span><svg class="skill-icon" width="16" height="16"><rect x="1" y="3" width="11" height="11" fill="none" stroke="#555" stroke-width="1.5"/><path d="M7 9l7-7" stroke="#555" stroke-width="2"/></svg><div class="skill-track"><div class="skill-fill" style="width:75%"></div></div><div class="skill-badge" style="left:146px">75%</div></div>
  <div class="skill abs" style="left:780px;top:180px"><span class="skill-label">Accounting</span><svg class="skill-icon" width="14" height="16"><rect x="1" y="1" width="12" height="14" fill="#555"/><rect x="3" y="3" width="8" height="3" fill="#ddd"/></svg><div class="skill-track"><div class="skill-fill" style="width:90%"></div></div><div class="skill-badge" style="left:164px">90%</div></div>

  <div class="skill abs" style="left:227px;top:289px"><span class="skill-label">Financial management</span><svg class="skill-icon" width="20" height="14"><path d="M1 7l5-4 4 3 4-3 5 4-5 5-4-3-4 3z" fill="none" stroke="#555" stroke-width="1.5"/></svg><div class="skill-track"><div class="skill-fill" style="width:50%"></div></div><div class="skill-badge" style="left:92px">50%</div></div>
  <div class="skill abs" style="left:503px;top:289px"><span class="skill-label">Project management</span><svg class="skill-icon" width="14" height="16"><circle cx="7" cy="5" r="4" fill="#555"/><path d="M1 15a6 6 0 0112 0z" fill="#555"/></svg><div class="skill-track"><div class="skill-fill" style="width:55%"></div></div><div class="skill-badge" style="left:103px">55%</div></div>
  <div class="skill abs" style="left:780px;top:289px"><span class="skill-label">Team player</span><svg class="skill-icon" width="18" height="14"><circle cx="5" cy="4" r="3" fill="#555"/><circle cx="13" cy="4" r="3" fill="#555"/><path d="M0 13a5 5 0 0110 0zM8 13a5 5 0 0110 0z" fill="#555"/></svg><div class="skill-track"><div class="skill-fill" style="width:55%"></div></div><div class="skill-badge" style="left:103px">55%</div></div>

  <div class="skill abs" style="left:227px;top:399px"><span class="skill-label">Trouble shooter</span><svg class="skill-icon" width="16" height="16"><circle cx="8" cy="8" r="6" fill="#555"/><circle cx="8" cy="8" r="2" fill="#ddd"/></svg><div class="skill-track"><div class="skill-fill" style="width:95%"></div></div><div class="skill-badge" style="left:175px">95%</div></div>
</section>

<section class="education">
  <h2 class="heading abs center" style="top:1866px">Education</h2>
  <div class="heading-rule" style="left:577px;top:1906px"></div>
  <div class="degrees-badge abs">SOME OF MY DEGREES</div>
  <div class="timeline-line abs"></div>

  <div class="edu-card abs" style="left:144px;top:2049px;width:409px;height:227px;text-align:right">
    <h3>NOVERA (RA)</h3>
    There are many variations of passages of Lorem Ipsum available, but the majority have suffered alteration in some form, by injected humour, or randomised words which don't look even slightly believable. If you are going to use a passage of Lorem Ipsum, you need to be sure there isn't anything embarrassing hidden in the middle of text
  </div>
  <div class="timeline-dot abs" style="left:590px;top:2150px"></div>
  <div class="year abs" style="left:625px;top:2149px">1996</div>

  <div class="edu-card abs" style="left:666px;top:2320px;width:410px;height:221px">
    <h3>LYCEUM B</h3>
    There are many variations of passages of Lorem Ipsum available, but the majority have suffered alteration in some form, by injected humour, or randomised words which don't look even slightly believable. If you are going to use a passage of Lorem Ipsum, you need to be sure there isn't anything embarrassing hidden in the middle of text
  </div>
  <div class="timeline-dot abs" style="left:590px;top:2412px"></div>
  <div class="year abs" style="left:517px;top:2411px">2001</div>
  <div class="timeline-end abs"></div>
</section>

<section class="portfolio-band abs">
  <h2 class="heading abs center" style="top:44px">Portfolio</h2>
  <div class="heading-rule" style="left:577px;top:84px;background:#666"></div>
</section>
<div class="tile abs" style="left:0;top:2845px;background:linear-gradient(160deg,#8fb07a,#4e6a3a)" role="img" aria-label="Photo of butterflies on yellow flowers"></div>
<div class="tile abs" style="left:300px;top:2845px;background:linear-gradient(180deg,#3b2b5e,#b05a78 50%,#2a1a30)" role="img" aria-label="Photo of a tree at a purple sunset"></div>
<div class="tile abs" style="left:600px;top:2845px;background:radial-gradient(circle at 50% 50%,#8aa24a,#c9b98a 55%,#a89a6a)" role="img" aria-label="Photo of a green leaf on sand"></div>
<div class="tile abs" style="left:900px;top:2845px;background:linear-gradient(180deg,#1a1630,#5a3a4a 60%,#1a1212)" role="img" aria-label="Photo of a rock arch under a starry sky"></div>
<div class="tile abs" style="left:0;top:3138px;background:linear-gradient(180deg,#5a6a6a,#2a3030)" role="img" aria-label="Photo of an elephant in misty light"></div>
<div class="tile abs" style="left:300px;top:3138px;background:radial-gradient(circle at 50% 60%,#e0405a,#5a1030 55%,#1a0a1a)" role="img" aria-label="Photo of a tree silhouette against a red sky"></div>
<div class="tile abs" style="left:600px;top:3138px;background:radial-gradient(circle at 50% 50%,#d0a050,#5a3a10 60%,#1a1208)" role="img" aria-label="Photo of a water droplet splash"></div>
<div class="tile abs" style="left:900px;top:3138px;background:linear-gradient(180deg,#6a5a4a,#b07a3a 55%,#4a3020)" role="img" aria-label="Photo of a mountain landscape at golden hour"></div>

<section class="contact abs">
  <h2 class="heading abs center" style="top:62px">Contact</h2>
  <div class="heading-rule" style="left:577px;top:102px"></div>
</section>
<p class="contact-text abs">There are many variations of passages of Lorem Ipsum available, but the majority have suffered alteration in some form, by injected humour, or randomised words which don't look even slightly believable. If you are going to use a passage of Lorem Ipsum, you need to be sure there isn't anything embarrassing.</p>
<div class="contact-item abs" style="top:3750px">
  <span class="contact-icon"><svg width="30" height="30"><path d="M11 9c1 0 2 3 2 4l-2 1c1 2 3 4 5 5l1-2c1 0 4 1 4 2 0 2-2 3-3 3-5-1-9-5-10-10 0-1 1-3 3-3z" fill="#fff"/></svg></span>
  <span class="contact-label">CALL US</span><span class="contact-value">888.888.8888</span>
</div>
<div class="contact-item abs" style="top:3835px">
  <span class="contact-icon"><svg width="30" height="30"><rect x="8" y="10" width="14" height="10" fill="#fff"/><path d="M8 10l7 6 7-6" fill="none" stroke="#000" stroke-width="1.2"/></svg></span>
  <span class="contact-label">EMAIL US</span><span class="contact-value" style="font-size:16px">contact@velmotbv.com</span>
</div>
<div class="field abs" style="left:523px;top:3606px;width:260px;height:44px">Your Name</div>
<div class="field abs" style="left:794px;top:3606px;width:259px;height:44px">Your Email</div>
<div class="field abs" style="left:523px;top:3666px;width:530px;height:177px">Your Message</div>
<div class="send-btn abs">SEND</div>

<footer class="site-footer abs">
  <div class="footer-brand abs">VELMOT BV</div>
  <div class="follow abs">FOLLOW US</div>
  <span class="social abs" style="left:598px" aria-label="Social profile one"></span>
  <span class="social abs" style="left:631px" aria-label="Social profile two"></span>
  <span class="social abs" style="left:666px" aria-label="Social profile three"></span>
  <div class="copyright abs">Copyrights @ 2018 All Rights Reserved</div>
</footer>

</body>
</html>
```